Home Page Design for Motor Manufacturer

Hello,
please design the homepage for a manufacturer of industry motors. I am looking for a professional, clean and minimalistic design. Since this a rather conservative industry it should get a professional look but since it is a redesign there should be some modern that gives is the modern touch of innovation.
A competitor's homepage I like is:
https://www.valdorix.example/en/
What I like about this website:
* clean, minimal, well structured design
* mega menu
For this project please find attached the wireframes (most buttons are in German but by context and Google translate you will easily figure it out; only unclear - "Messe" means "trade exhibition"). The paddings and margins are NOT exact. Also any color of backgrounds etc. chosen is not meant to represent a real color but rather to illustrate the object and maybe show there should be some background emphasis (color or image).
Wireframes:
https: //www.filnest. example / t / pQmW7zKtRb3LyaHx
In both wireframes the only thing that is different is the Service section. I expect from the winner both designs for this service section: one with normal cart design and one with tabs as filters to search products (find image for product categories attached)
In the header use on the left the following text:
h1: "Your competent partner for industrial engines,
-transmission and drawing parts
with more than 5000 satisfied customers "
primary button: Our products
sec. button: Download catalog
and on the right side we feature one or more product images (like putting them in a nice display together).
I also think of a solid background color or subtle gradient for the hero section.
The winner should also design an open mega menu version.
Menu items in this order:
• Home page
• Gearboxes & Motors
• Engine components
• Drawing parts
• Machines & accessories
• About us
• Contact
Also create a language switch with globe symbol and DE for Germany and EN for English above the nav plus the telephone number with icon (user dummy number +49 (0) 987654321)
Output should be in Figma, Sketch or PSD.
Fonts + color to use:
header: Proza Libre, bold, # 0171A1
body: Open Sans, regular, black
Primary accent color: # 0171A1
Text black or dark gray
background: light gray, white or shade of blue
More image resources:
https://www.filnest.example/t/ZuTn4VcqMh8ErwJo
If there are any questions please do not hesitate to ask.
Target Market(s)
B2B - anyone with industrial machinery needing small motors (not car engines)
Industry/Entity Type
Manufacturing
Number of Pages Required
1 page
Requirements
Must have
- see above
Nice to have
- see above
Should not have
- see above

```html
<!DOCTYPE html>
<html lang="en">
<head>
<meta charset="utf-8">
<title>Korvant – Industrial Motors & Gearboxes</title>
<link href="https://fonts.googleapis.com/css2?family=Open+Sans:wght@400;600;700&family=Proza+Libre:wght@500;600;700&display=swap" rel="stylesheet">
<style>
:root{
  --primary:#0171a1;
  --primary-deep:#0b5f91;
  --hero-top:#1179b0;
  --hero-bottom:#0a5d8f;
  --navy:#0c4a74;
  --ink:#1e1e1e;
  --text:#444;
  --muted:#777;
  --line:#d8d8d8;
  --card-grey:#f1f1f1;
  --section-grey:#f3f2f2;
  --band-blue:#dfe6ee;
  --dark-btn:#3b3b3b;
  --footer:#1c2236;
  --white:#fff;
}
*{box-sizing:border-box;margin:0;padding:0}
html,body{width:1200px;height:4906px;overflow:hidden}
body{font-family:"Open Sans",sans-serif;color:var(--ink);background:var(--white);position:relative}
h1,h2,h3,.heading{font-family:"Proza Libre",sans-serif}
.abs{position:absolute}
section,header,footer,nav{position:absolute;left:0;width:1200px}

/* top bar */
.topbar{top:0;height:72px;background:var(--white)}
.brand{left:120px;top:14px;font-family:"Proza Libre",sans-serif;font-weight:700;font-size:32px;line-height:42px;color:var(--navy);display:flex;align-items:center;gap:10px;white-space:nowrap}
.brand .dot{width:14px;height:14px;background:var(--primary);border-radius:50%}
.top-phone{left:818px;top:26px;font-size:14px;line-height:20px;color:var(--primary);display:flex;align-items:center;gap:6px;white-space:nowrap}
.lang{left:1019px;top:23px;width:60px;height:28px;border:1px solid var(--line);font-size:12px;color:#555;display:flex;align-items:center;justify-content:center;gap:10px}
.mainnav{top:72px;height:56px;background:#f7f7f7;border-bottom:1px solid #e4e4e4}
.mainnav a{position:absolute;top:18px;font-size:14px;line-height:20px;color:#333;text-decoration:none;white-space:nowrap}
.mainnav a.active{color:var(--primary)}
.mainnav a .caret{font-size:9px;color:#888;margin-left:5px}

/* hero */
.hero{top:128px;height:622px;background:linear-gradient(180deg,var(--hero-top),var(--hero-bottom));overflow:hidden}
.hero h1{position:absolute;left:120px;top:166px;font-size:36px;line-height:51px;font-weight:700;color:var(--white)}
.hero .lead{position:absolute;left:120px;top:296px;font-size:19px;line-height:34px;color:#e6f1f8}
.btn{position:absolute;display:flex;align-items:center;justify-content:center;border-radius:22px;font-size:16px;color:var(--white);text-decoration:none}
.btn-dark{background:#0d3f63}
.btn-outline{border:2px solid var(--white)}
.hero-shot{left:646px;top:103px;width:362px;height:362px;border-radius:50%;background:var(--white);border:12px solid #27a3d8}
.hero-shot div{width:100%;height:100%;border-radius:50%;background:radial-gradient(circle at 50% 45%,#c9d2d9,#5a6a78 55%,#ffffff 70%)}
.thumb{left:1029px;width:60px;height:60px;border-radius:50%;background:radial-gradient(circle,#a9b6c1,#4a6476);border:3px solid #bfe3f3}
.thumb.current{border-color:var(--white);background:radial-gradient(circle,#dfe6eb,#6e8595)}

/* why choose */
.section-title{position:absolute;left:0;width:1200px;text-align:center;font-family:"Proza Libre",sans-serif;font-weight:500;font-size:44px;color:var(--ink)}
.section-intro{position:absolute;left:240px;width:720px;text-align:center;font-size:14px;line-height:27px;color:#333}
.feature{position:absolute;top:1019px;height:204px;background:var(--card-grey);text-align:center}
.feature .icon{position:absolute;left:50%;top:32px;transform:translateX(-50%)}
.feature h3{position:absolute;left:0;width:100%;top:128px;font-family:"Open Sans",sans-serif;font-weight:600;font-size:19px;color:#333}
.feature.featured{top:987px;height:270px;background:var(--primary);box-shadow:0 8px 18px rgba(0,0,0,.2);color:var(--white)}
.feature.featured h3{top:96px;color:var(--white);font-size:19px}
.feature.featured p{position:absolute;left:28px;right:28px;top:136px;font-size:12.5px;line-height:24px}

/* product categories */
.cat-card{position:absolute;top:1474px;height:250px;width:225px;border:1px solid #e3e3e3;background:var(--white);box-shadow:0 2px 6px rgba(0,0,0,.05)}
.cat-card.featured{border:2px solid var(--primary)}
.product-shot{position:absolute;left:50%;transform:translateX(-50%);border-radius:50%;background:radial-gradient(circle at 45% 45%,#e8ecef,#7d8a95 55%,#2e3840 72%,rgba(255,255,255,0) 74%)}
.cat-card .product-shot{top:24px;width:150px;height:150px}
.cat-card span{position:absolute;top:196px;width:100%;text-align:center;font-size:16px;color:#222}

.filter{position:absolute;left:133px;top:1864px;font-size:17px;color:#555;display:flex;align-items:center;gap:8px}
.pill{position:absolute;top:1859px;height:37px;border:1px solid #bbb;border-radius:19px;font-size:15px;color:#555;display:flex;align-items:center;justify-content:center}
.pill.active{background:var(--primary);border-color:var(--primary);color:var(--white)}
.filter-rule{position:absolute;left:120px;top:1924px;width:960px;height:1px;background:#cfd6dc}
.grid-band{top:1925px;height:865px;background:var(--section-grey)}
.item-card{position:absolute;width:270px;height:308px;background:var(--white);border:1px solid #e4e4e4}
.item-card.featured{border:2px solid var(--primary)}
.item-card .product-shot{top:22px;width:170px;height:170px}
.item-card h3{position:absolute;top:220px;width:100%;text-align:center;font-family:"Open Sans",sans-serif;font-weight:600;font-size:19px;color:#222}
.item-card .details{position:absolute;left:75px;width:120px;top:280px;height:36px;background:var(--dark-btn);color:var(--white);font-size:16px;display:flex;align-items:center;justify-content:center}
.item-card.featured .details{background:var(--primary)}

/* exhibition */
.expo{position:absolute;top:2981px;width:300px;height:398px;background:var(--card-grey)}
.expo .photo{position:absolute;left:0;width:300px;height:199px;background:linear-gradient(160deg,#39507a 0%,#8d8a7f 55%,#2b3c6a 100%)}
.expo .body{position:absolute;left:29px;width:250px}
.expo h3{font-family:"Open Sans",sans-serif;font-weight:600;font-size:16px;color:#222;margin-bottom:10px}
.expo p{font-size:12.5px;line-height:24px;color:#666;margin-bottom:12px}
.expo .actions{display:flex;gap:9px}
.expo .actions span{height:30px;padding:0 16px;font-size:14px;color:var(--white);display:flex;align-items:center}
.tag-blue{background:#1a87c4}
.tag-navy{background:var(--navy)}
.view-more{position:absolute;left:524px;top:3427px;width:152px;height:50px;background:var(--navy);color:var(--white);font-size:18px;display:flex;align-items:center;justify-content:center}

/* about */
.about{top:3578px;height:588px;background:var(--section-grey)}
.about .frame{position:absolute;left:151px;top:117px;width:348px;height:368px;border:5px solid var(--primary-deep);border-left:none;border-top:none}
.about .photo{position:absolute;left:120px;top:81px;width:347px;height:368px;background:linear-gradient(150deg,#6d4a2e,#c49a3a 40%,#3e6e54 75%,#2d3c4c)}
.about h2{position:absolute;left:575px;top:90px;font-weight:500;font-size:36px;color:var(--ink)}
.about .strong{position:absolute;left:575px;top:155px;width:500px;font-size:16px;line-height:27px;font-weight:600;color:#333}
.about .copy{position:absolute;left:575px;top:225px;width:475px;font-size:14px;line-height:25.7px;color:#555}
.about .btn-sq{position:absolute;left:575px;top:428px;width:153px;height:48px;background:var(--primary-deep);color:var(--white);font-size:18px;display:flex;align-items:center;justify-content:center}

/* catalog */
.catalog{top:4166px;height:267px;background:var(--band-blue);overflow:hidden}
.catalog h2{position:absolute;right:646px;top:42px;font-weight:500;font-size:40px;letter-spacing:.5px;color:#222;white-space:nowrap}
.catalog p{position:absolute;right:646px;top:106px;width:440px;text-align:right;font-size:17px;line-height:29px;color:#222}
.catalog .dl{position:absolute;left:375px;top:177px;width:179px;height:39px;border-radius:20px;background:var(--primary);color:var(--white);font-size:16px;display:flex;align-items:center;justify-content:center}
.catalog .divider{position:absolute;left:602px;top:48px;width:1px;height:170px;background:#b9c5d2}

/* contact strip */
.contacts{top:4433px;height:187px;background:var(--white)}
.contact{position:absolute;top:72px;display:flex;align-items:center;gap:16px}
.contact small{display:block;font-size:12px;font-weight:600;color:#333;margin-bottom:6px}
.contact b{font-size:18px;color:var(--primary-deep);font-weight:600;white-space:nowrap}
.contact span{font-size:12px;line-height:17px;color:#333;display:block;font-weight:600}
.contacts .sep{position:absolute;top:60px;width:1px;height:90px;background:#ddd}

/* footer */
.site-footer{top:4620px;height:286px;background:var(--footer);color:#cfd3dd}
.site-footer .brand{left:120px;top:40px;color:var(--white);font-size:44px;line-height:56px}
.site-footer .brand .dot{background:var(--white)}
.news-label{position:absolute;left:122px;top:120px;font-size:13px;color:var(--white)}
.news{position:absolute;left:120px;top:152px;width:270px;height:32px;border-radius:16px;overflow:hidden;display:flex}
.news span{flex:1;background:var(--white);font-size:11px;color:#888;display:flex;align-items:center;padding-left:22px}
.news b{width:102px;background:var(--primary);color:var(--white);font-size:13px;font-weight:600;display:flex;align-items:center;justify-content:center}
.fcol{position:absolute;top:44px}
.fcol h4{font-family:"Open Sans",sans-serif;font-weight:400;font-size:15px;color:var(--white);margin-bottom:14px}
.fcol li{list-style:none;font-size:13px;line-height:24px;color:#c5cad6}
.ask{position:absolute;left:857px;top:50px;width:240px}
.ask h4{font-weight:400;font-size:15px;color:var(--white);margin-bottom:14px;font-family:"Open Sans",sans-serif}
.ask p{font-size:13px;line-height:22px;color:#c5cad6}
.ask .call{margin-top:14px;width:175px;height:42px;background:var(--primary);color:var(--white);font-size:14px;font-weight:600;display:flex;align-items:center;gap:14px;padding-left:6px}
.ask .call i{width:34px;height:34px;border-radius:50%;background:#0f1526;display:flex;align-items:center;justify-content:center}
.legal-rule{position:absolute;left:0;top:220px;width:1200px;height:1px;background:#2c3349}
.legal{position:absolute;top:244px;font-size:12px;color:#aab0c0}
</style>
</head>
<body>

<header class="topbar">
  <div class="abs brand">Korvant<span class="dot"></span></div>
  <div class="abs top-phone">
    <svg width="18" height="18" viewBox="0 0 24 24" fill="none" stroke="currentColor" stroke-width="2"><path d="M5 3h4l2 5-3 2a12 12 0 0 0 6 6l2-3 5 2v4a2 2 0 0 1-2 2A17 17 0 0 1 3 5a2 2 0 0 1 2-2z"/></svg>
    +49 (0) 987654321
  </div>
  <div class="abs lang">EN <span style="font-size:8px;color:#999">▼</span></div>
</header>

<nav class="mainnav">
  <a class="active" style="left:120px">Home</a>
  <a style="left:192px">Gearboxes &amp; Motors<span class="caret">▼</span></a>
  <a style="left:385px">Engine Components<span class="caret">▼</span></a>
  <a style="left:573px">Drawing parts<span class="caret">▼</span></a>
  <a style="left:720px">Machines &amp; Accessories<span class="caret">▼</span></a>
  <a style="left:932px">About Us</a>
  <a style="left:1027px">Contact</a>
</nav>

<section class="hero">
  <svg class="abs" style="left:0;top:0" width="1200" height="622" viewBox="0 0 1200 622">
    <path d="M0 330 C300 250 600 420 1200 300 L1200 622 L0 622Z" fill="#ffffff" opacity=".05"/>
    <path d="M0 420 C350 330 750 500 1200 380 L1200 622 L0 622Z" fill="#ffffff" opacity=".05"/>
    <path d="M0 622 L0 600 C260 560 520 530 760 548 C960 562 1100 548 1200 520 L1200 622Z" fill="#ffffff"/>
  </svg>
  <h1>Your Competent Partner<br>For Industrial Engines</h1>
  <p class="lead">Transmission And Drawing Parts<br>With More Than 5000 Satisfied Customers</p>
  <a class="btn btn-dark" style="left:120px;top:394px;width:156px;height:42px">Learn More</a>
  <a class="btn btn-outline" style="left:290px;top:394px;width:154px;height:42px">All Products</a>
  <div class="abs hero-shot"><div role="img" aria-label="Planetary gearbox with blue-labelled motor"></div></div>
  <svg class="abs" style="left:1049px;top:142px" width="20" height="12" viewBox="0 0 20 12"><path d="M2 10 L10 2 L18 10" fill="none" stroke="#ffffff" stroke-width="1.5" opacity=".7"/></svg>
  <div class="abs thumb" style="top:185px" role="img" aria-label="Gearbox thumbnail"></div>
  <div class="abs thumb current" style="top:261px" role="img" aria-label="Motor thumbnail"></div>
  <div class="abs thumb" style="top:341px" role="img" aria-label="Geared motor thumbnail"></div>
</section>

<section style="top:750px;height:1174px">
  <h2 class="section-title" style="top:54px">Why Choose Us</h2>
  <p class="section-intro" style="top:132px">Lorem Ipsum is simply dummy text of the printing and typesetting industry. Lorem Ipsum has been the industry's standard dummy text ever since the 1500s Lorem Ipsum is simply dummy</p>
</section>

<div class="feature" style="left:0;width:284px">
  <svg class="icon" width="80" height="80" viewBox="0 0 80 80" fill="#1a75b3"><circle cx="40" cy="16" r="10" fill="none" stroke="#1a75b3" stroke-width="4"/><path d="M22 44a18 14 0 0 1 36 0" fill="none" stroke="#1a75b3" stroke-width="4"/><path d="M18 48l4 9 9 1-7 6 2 9-8-5-8 5 2-9-7-6 9-1z"/><path d="M40 48l4 9 9 1-7 6 2 9-8-5-8 5 2-9-7-6 9-1z"/><path d="M62 48l4 9 9 1-7 6 2 9-8-5-8 5 2-9-7-6 9-1z"/></svg>
  <h3>Customer Satisfaction</h3>
</div>
<div class="feature featured" style="left:299px;width:301px">
  <svg class="icon" style="top:28px" width="52" height="52" viewBox="0 0 52 52" fill="none" stroke="#ffffff" stroke-width="2.5"><circle cx="26" cy="26" r="22"/><circle cx="26" cy="26" r="15"/><text x="26" y="32" text-anchor="middle" font-size="17" fill="#ffffff" stroke="none" font-family="Open Sans">$</text></svg>
  <h3>Optimal Price</h3>
  <p>Lorem Ipsum is simply dummy text of the printing and typesetting industry. Lorem Ipsum has been.</p>
  <svg class="abs" style="left:137px;top:222px" width="26" height="26" viewBox="0 0 26 26" fill="none" stroke="#ffffff" stroke-width="1.6"><circle cx="13" cy="13" r="11"/><path d="M8 11l5 5 5-5"/></svg>
</div>
<div class="feature" style="left:615px;width:284px">
  <svg class="icon" width="84" height="80" viewBox="0 0 84 80" fill="#1a75b3"><circle cx="28" cy="38" r="16"/><circle cx="28" cy="38" r="6" fill="#f1f1f1"/><circle cx="60" cy="20" r="11"/><circle cx="60" cy="20" r="4" fill="#f1f1f1"/><circle cx="62" cy="58" r="11"/><circle cx="62" cy="58" r="4" fill="#f1f1f1"/></svg>
  <h3>Smooth Implementation</h3>
</div>
<div class="feature" style="left:916px;width:284px">
  <svg class="icon" width="76" height="84" viewBox="0 0 76 84" fill="#1a75b3"><circle cx="38" cy="32" r="28"/><circle cx="38" cy="32" r="19" fill="#f1f1f1"/><path d="M38 20l4 8 9 1-7 6 2 9-8-5-8 5 2-9-7-6 9-1z"/><path d="M16 54l-8 22 12-4 6 10 8-20z"/><path d="M60 54l8 22-12-4-6 10-8-20z"/></svg>
  <h3>High Quality</h3>
</div>

<h2 class="section-title" style="top:1378px">Our Products</h2>
<div class="cat-card" style="left:120px"><div class="product-shot" role="img" aria-label="Right-angle gearbox"></div><span>Product Category</span></div>
<div class="cat-card featured" style="left:366px"><div class="product-shot" role="img" aria-label="Planetary gearbox motor"></div><span>Product Category</span></div>
<div class="cat-card" style="left:611px"><div class="product-shot" role="img" aria-label="DC geared motor"></div><span>Product Category</span></div>
<div class="cat-card" style="left:855px"><div class="product-shot" role="img" aria-label="Harmonic drive reducer"></div><span>Product Category</span></div>

<div class="filter">
  <svg width="20" height="20" viewBox="0 0 24 24" fill="none" stroke="#555" stroke-width="1.6"><path d="M3 4h18l-7 8v7l-4 2v-9z"/></svg>
  Filter :
</div>
<div class="pill" style="left:257px;width:156px">Sub Category</div>
<div class="pill active" style="left:432px;width:160px">Sub Category</div>
<div class="pill" style="left:608px;width:160px">Sub Category</div>
<div class="pill" style="left:783px;width:160px">Sub Category</div>
<div class="filter-rule"></div>

<section class="grid-band">
  <div class="item-card" style="left:164px;top:81px"><div class="product-shot" role="img" aria-label="Right-angle gearbox"></div><h3>Product Title</h3><div class="details">Details</div></div>
  <div class="item-card featured" style="left:465px;top:81px"><div class="product-shot" role="img" aria-label="Planetary gearbox motor"></div><h3>Product Title</h3><div class="details">Details</div></div>
  <div class="item-card" style="left:768px;top:81px"><div class="product-shot" role="img" aria-label="DC geared motor"></div><h3>Product Title</h3><div class="details">Details</div></div>
  <div class="item-card" style="left:164px;top:431px"><div class="product-shot" role="img" aria-label="Harmonic drive reducer"></div><h3>Product Title</h3><div class="details">Details</div></div>
  <div class="item-card" style="left:465px;top:431px"><div class="product-shot" role="img" aria-label="Inline gearbox motor"></div><h3>Product Title</h3><div class="details">Details</div></div>
  <div class="item-card" style="left:768px;top:431px"><div class="product-shot" role="img" aria-label="Right-angle gearbox"></div><h3>Product Title</h3><div class="details">Details</div></div>
</section>

<h2 class="section-title" style="top:2888px">Trade Exhibition</h2>
<div class="expo" style="left:120px">
  <div class="photo" style="top:0" role="img" aria-label="Crowded trade fair hall with exhibitor stands"></div>
  <div class="body" style="top:224px"><h3>Trade Exhibition</h3><p>Lorem Ipsum is simply dummy text of the printing and typesetting industry.</p><div class="actions"><span class="tag-blue">Free tickets</span><span class="tag-navy">Details</span></div></div>
</div>
<div class="expo" style="left:451px">
  <div class="body" style="top:24px"><h3>Trade Exhibition</h3><p>Lorem Ipsum is simply dummy text of the printing and typesetting industry.</p><div class="actions"><span class="tag-blue">Free tickets</span><span class="tag-navy">Details</span></div></div>
  <div class="photo" style="top:199px" role="img" aria-label="Visitors walking through an exhibition hall"></div>
</div>
<div class="expo" style="left:783px">
  <div class="photo" style="top:0;background:linear-gradient(160deg,#2c3a52,#b7b9b0 50%,#4a5c6c)" role="img" aria-label="Exhibition stands in a bright hall"></div>
  <div class="body" style="top:224px"><h3>Trade Exhibition</h3><p>Lorem Ipsum is simply dummy text of the printing and typesetting industry.</p><div class="actions"><span class="tag-blue">Free tickets</span><span class="tag-navy">Details</span></div></div>
</div>
<div class="view-more">View More</div>

<section class="about">
  <div class="frame"></div>
  <div class="photo" role="img" aria-label="Technician in hard hat working at a lathe"></div>
  <h2>About Us</h2>
  <p class="strong">Lorem Ipsum is simply dummy text of the printing and typesetting industry.</p>
  <p class="copy">Lorem Ipsum has been the industry's standard dummy text ever since the 1500 Lorem Ipsum is simply dummy text of the printing and typesetting industry. Lorem Ipsum has been the industry's standard dummy text ever since the 1500s. Lorem Ipsum is simply dummy text of the printing and typesetting industry. Lorem Ipsum has been the industry's standard dummy text ever since the 1500s. Lorem Ipsum is simply dummy text of the printing.</p>
  <div class="btn-sq">Learn More</div>
</section>

<section class="catalog">
  <svg class="abs" style="left:620px;top:0" width="580" height="267" viewBox="0 0 580 267" fill="#c9d3de" opacity=".7">
    <circle cx="60" cy="70" r="4"/><circle cx="70" cy="120" r="5"/><circle cx="40" cy="150" r="3"/><circle cx="48" cy="210" r="18"/>
    <circle cx="330" cy="60" r="9"/><circle cx="340" cy="170" r="6"/><circle cx="410" cy="120" r="4"/><circle cx="456" cy="100" r="20"/><circle cx="500" cy="80" r="4"/>
  </svg>
  <h2>Download Catalog</h2>
  <p>Lorem Ipsum is simply dummy text of the printing and typesetting industry</p>
  <div class="dl">Download Now</div>
  <div class="divider"></div>
  <svg class="abs" style="left:708px;top:34px" width="188" height="188" viewBox="0 0 188 188">
    <circle cx="94" cy="94" r="91" fill="none" stroke="#b7c3d0" stroke-width="1.5"/>
    <rect x="58" y="58" width="60" height="76" fill="#0f5a8c"/>
    <path d="M66 76h40M66 88h40M66 100h40M66 112h30" stroke="#ffffff" stroke-width="3"/>
    <path d="M114 38v34M102 60l12 12 12-12" fill="none" stroke="#0f5a8c" stroke-width="7"/>
  </svg>
</section>

<section class="contacts">
  <div class="contact" style="left:168px">
    <svg width="48" height="48" viewBox="0 0 48 48" fill="none" stroke="#1a75b3" stroke-width="2"><path d="M10 6h8l4 10-6 4a24 24 0 0 0 12 12l4-6 10 4v8a4 4 0 0 1-4 4A34 34 0 0 1 6 10a4 4 0 0 1 4-4z"/><path d="M30 8a12 12 0 0 1 10 10M30 14a6 6 0 0 1 4 4"/></svg>
    <div><small>CALL Now</small><b>+49 (0) 987654321</b></div>
  </div>
  <div class="sep" style="left:436px"></div>
  <div class="contact" style="left:522px">
    <svg width="48" height="48" viewBox="0 0 48 48" fill="none" stroke="#1a75b3" stroke-width="2"><path d="M24 4a12 12 0 0 1 12 12c0 9-12 22-12 22S12 25 12 16A12 12 0 0 1 24 4z"/><circle cx="24" cy="16" r="5"/><path d="M8 36l-4 8h40l-4-8"/></svg>
    <div><small>ADDRESS</small><span>Address, Lorem<br>Ipsum is simply</span></div>
  </div>
  <div class="sep" style="left:752px"></div>
  <div class="contact" style="left:832px">
    <svg width="48" height="48" viewBox="0 0 48 48" fill="none" stroke="#1a75b3" stroke-width="2"><rect x="6" y="14" width="36" height="26"/><path d="M6 14l18 14 18-14"/><path d="M14 10V6h20v4"/></svg>
    <div><small>E-MAIL</small><span>info@korvant.example</span></div>
  </div>
</section>

<footer class="site-footer">
  <div class="abs brand">Korvant<span class="dot"></span></div>
  <p class="news-label">Subscribe to our newsletter</p>
  <div class="news"><span>Email address</span><b>Subscribe</b></div>
  <div class="fcol" style="left:450px"><h4>Quick Links</h4><ul><li>Home</li><li>Gearboxes &amp; Motors</li><li>Engine Components</li><li>Drawing Parts</li><li>Machines &amp; Accessories</li></ul></div>
  <div class="fcol" style="left:669px"><h4>Category</h4><ul><li>Category Name</li><li>Category Name</li><li>Category Name</li><li>Category Name</li><li>Category Name</li></ul></div>
  <div class="ask">
    <h4>Stil have questions?</h4>
    <p>A repesentative will aswer your questions as soon as possible.</p>
    <div class="call"><i><svg width="18" height="18" viewBox="0 0 24 24" fill="none" stroke="#ffffff" stroke-width="2"><path d="M5 3h4l2 5-3 2a12 12 0 0 0 6 6l2-3 5 2v4a2 2 0 0 1-2 2A17 17 0 0 1 3 5a2 2 0 0 1 2-2z"/></svg></i>Contact Now</div>
  </div>
  <div class="legal-rule"></div>
  <p class="legal" style="left:131px">Copyright 2020 Korvant. All Rights Reserved.</p>
  <p class="legal" style="left:851px">Privacy Policy &nbsp; | &nbsp; Terms Of Services</p>
</footer>

</body>
</html>
```